Typography of the cover "Watch the tide turning"

We would like to improve the presentation of a book cover: presentation and typography of the authors and of the title. Image of the cover is available in two versions (with or without sky), joined with the texts (joined files): Mathis Corvenot Watched the turning tide Romance Editions Murlane

Industry/Entity Type

Publishing

Colors

Designer to choose colors to be used in the design.

Requirements
Must have
• Provided picture (with or without sky)

```html
<!DOCTYPE html>
<html lang="en">
<head>
<meta charset="utf-8">
<title>Watch the tide turning — Mathis Corvenot</title>
<link rel="stylesheet" href="https://fonts.googleapis.com/css2?family=Jost:wght@500;600;700&display=swap">
<style>
  :root {
    --paper: #ececec;
    --paper-light: #f3f3f3;
    --ink: #2b2b2b;
    --title-red: #c93032;
    --city-dark: #2e2e2e;
    --city-mid: #6f6f6f;
    --city-light: #b9b9b9;
    --white: #ffffff;
  }
  html, body {
    margin: 0;
    padding: 0;
    width: 810px;
    height: 1200px;
    overflow: hidden;
    background: var(--paper);
  }
  .cover {
    position: relative;
    width: 810px;
    height: 1200px;
    overflow: hidden;
    background: linear-gradient(180deg, var(--paper-light) 0%, var(--paper) 45%, var(--paper) 100%);
    font-family: "Jost", "Futura", sans-serif;
  }
  .cityscape {
    position: absolute;
    left: 0;
    top: 500px;
    width: 810px;
    height: 700px;
    background:
      linear-gradient(180deg, rgba(236,236,236,1) 0%, rgba(236,236,236,0) 28%),
      repeating-linear-gradient(90deg, rgba(255,255,255,0.10) 0 6px, rgba(0,0,0,0.08) 6px 14px, rgba(255,255,255,0.05) 14px 23px),
      linear-gradient(180deg, var(--city-light) 0%, var(--city-mid) 40%, var(--city-dark) 100%);
  }
  .line {
    position: absolute;
    left: 0;
    width: 810px;
    margin: 0;
    text-align: center;
    line-height: 1;
    text-transform: uppercase;
    white-space: nowrap;
  }
  .author-first { top: 78px; font-size: 26px; font-weight: 600; letter-spacing: 2px; color: var(--ink); }
  .author-last { top: 118px; font-size: 44px; font-weight: 600; letter-spacing: 4px; color: var(--ink); }
  .title-small { top: 265px; font-size: 31px; font-weight: 700; color: var(--title-red); }
  .title-medium { top: 322px; font-size: 84px; font-weight: 700; color: var(--title-red); }
  .title-large { top: 425px; font-size: 136px; font-weight: 700; color: var(--title-red); letter-spacing: -1px; }
  .genre { top: 660px; font-size: 22px; font-weight: 600; letter-spacing: 2px; color: var(--ink); }
  .publisher { top: 1122px; font-size: 24px; font-weight: 600; letter-spacing: 2px; color: var(--white); }
</style>
</head>
<body>
  <main class="cover">
    <div class="cityscape" role="img" aria-label="Black and white aerial photograph of a dense city skyline, blurred with vertical motion streaks fading into the pale sky"></div>
    <p class="line author-first">Mathis</p>
    <p class="line author-last">Corvenot</p>
    <h1 class="title">
      <span class="line title-small">Watch</span>
      <span class="line title-medium">The Tide</span>
      <span class="line title-large">Turning</span>
    </h1>
    <p class="line genre">Roman</p>
    <p class="line publisher">Editions Murlane</p>
  </main>
</body>
</html>
```